Business card for Internet Marketing Consultant

Simple - need a nice business card design using the logo elements and colors. Keywords: Progressive, professional, stylish, minimalist. Please use the nb as part of the design.

Info for card:

Brendan Okafor
Internet Marketing Strategist
Phone: (602) 555-0148
Email: brendan@northbeamgrowth.com
Address: 2193 W. Larkmoor Ave., Ste. 118
Kessler Falls, Arizona 85399

Website: www.northbeamgrowth.com

Industry/Entity Type

Business

Font styles to use
Sans Serif

```html
<!DOCTYPE html>
<html lang="en">
<head>
<meta charset="utf-8">
<title>North Beam Growth – Business Card</title>
<link href="https://fonts.googleapis.com/css2?family=Tinos:wght@400;700&family=Montserrat:wght@400&display=swap" rel="stylesheet">
<style>
  :root {
    --green: #55bd66;
    --blue: #1a4fb8;
    --white: #f7faf9;
    --grey: #8a8f95;
    --backdrop: #e6e8ea;
  }
  * { margin: 0; padding: 0; box-sizing: border-box; }
  html, body { width: 1200px; height: 960px; overflow: hidden; }
  body {
    background: var(--backdrop);
    font-family: "Tinos", "Times New Roman", serif;
    position: relative;
  }
  .card {
    position: absolute;
    left: 250px;
    width: 700px;
    height: 400px;
    overflow: hidden;
    box-shadow: 0 6px 18px rgba(0,0,0,.18);
    background: var(--white);
  }
  .card--front { top: 60px; }
  .card--back { top: 500px; }
  .card-art { position: absolute; inset: 0; width: 100%; height: 100%; }

  .wordmark { position: absolute; }
  .wordmark__name {
    display: flex; align-items: center; gap: 10px;
    font-family: "Tinos", serif; font-weight: 700;
    color: var(--blue); line-height: 1;
  }
  .wordmark__square { background: var(--green); display: inline-block; }
  .wordmark__tagline {
    font-family: "Montserrat", sans-serif; font-weight: 400;
    color: var(--grey); text-transform: uppercase;
  }
  .card--front .wordmark { left: 180px; top: 130px; }
  .card--front .wordmark__name { font-size: 40px; }
  .card--front .wordmark__square { width: 22px; height: 22px; }
  .card--front .wordmark__tagline { font-size: 11px; letter-spacing: 4px; margin: 8px 0 0 32px; }

  .card--back .wordmark { left: 60px; top: 95px; }
  .card--back .wordmark__name { font-size: 50px; }
  .card--back .wordmark__square { width: 28px; height: 28px; }
  .card--back .wordmark__tagline { font-size: 13px; letter-spacing: 5px; margin: 10px 0 0 40px; }

  .band {
    position: absolute; left: 0; right: 0; top: 205px; height: 46px;
    background: var(--blue); color: var(--white);
    display: flex; justify-content: space-between; align-items: center;
    padding: 0 40px 0 60px;
  }
  .band__name { font-size: 22px; font-weight: 700; letter-spacing: .5px; }
  .band__title { font-size: 17px; }

  .contact-area {
    position: absolute; left: 0; right: 0; top: 251px; bottom: 0;
    background: var(--green); color: var(--white);
    display: flex; justify-content: space-between;
    padding: 38px 40px 0 60px; font-size: 16px;
  }
  .contact-list { list-style: none; display: flex; flex-direction: column; gap: 20px; }
  .contact-item { display: flex; align-items: flex-start; gap: 14px; line-height: 1.35; }
  .contact-item svg { width: 18px; height: 18px; flex: none; margin-top: 1px; fill: var(--white); }
</style>
</head>
<body>

  <section class="card card--front" aria-label="Card front">
    <svg class="card-art" viewBox="0 0 700 400" aria-hidden="true">
      <rect width="700" height="400" fill="var(--green)"/>
      <path d="M0,0 H700 V50 C600,260 400,370 220,360 C100,352 30,260 0,150 Z" fill="var(--blue)" transform="translate(0,14)"/>
      <path d="M0,0 H700 V50 C600,260 400,370 220,360 C100,352 30,260 0,150 Z" fill="var(--white)"/>
    </svg>
    <div class="wordmark">
      <div class="wordmark__name"><span class="wordmark__square"></span>northbeamgrowth</div>
      <div class="wordmark__tagline">Internet Marketing Strategies</div>
    </div>
  </section>

  <section class="card card--back" aria-label="Card back">
    <div class="wordmark">
      <div class="wordmark__name"><span class="wordmark__square"></span>northbeamgrowth</div>
      <div class="wordmark__tagline">Internet Marketing Strategies</div>
    </div>

    <div class="band">
      <span class="band__name">Brendan Okafor</span>
      <span class="band__title">Internet Marketing Strategist</span>
    </div>

    <div class="contact-area">
      <ul class="contact-list">
        <li class="contact-item">
          <svg viewBox="0 0 24 24" aria-label="Phone"><path d="M6.6 10.8a15.1 15.1 0 0 0 6.6 6.6l2.2-2.2c.3-.3.7-.4 1-.2 1.1.4 2.3.6 3.6.6.6 0 1 .4 1 1V20c0 .6-.4 1-1 1A17 17 0 0 1 3 4c0-.6.4-1 1-1h3.5c.6 0 1 .4 1 1 0 1.3.2 2.5.6 3.6.1.3 0 .7-.2 1z"/></svg>
          <span>(602) 555-0148</span>
        </li>
        <li class="contact-item">
          <svg viewBox="0 0 24 24" aria-label="Email"><path d="M2 5h20v14H2z M3.5 6.5 12 13l8.5-6.5" fill="none" stroke="var(--white)" stroke-width="2"/></svg>
          <span>brendan@northbeamgrowth.com</span>
        </li>
      </ul>
      <ul class="contact-list">
        <li class="contact-item">
          <svg viewBox="0 0 24 24" aria-label="Address"><path d="M12 2a7 7 0 0 0-7 7c0 5.2 7 13 7 13s7-7.8 7-13a7 7 0 0 0-7-7zm0 9.5A2.5 2.5 0 1 1 12 6.5a2.5 2.5 0 0 1 0 5z"/></svg>
          <span>2193 W. Larkmoor Ave., Ste. 118<br>Kessler Falls, Arizona 85399</span>
        </li>
        <li class="contact-item">
          <svg viewBox="0 0 24 24" aria-label="Website"><g fill="none" stroke="var(--white)" stroke-width="2"><circle cx="12" cy="12" r="9"/><path d="M3 12h18M12 3c3 3 3 15 0 18M12 3c-3 3-3 15 0 18"/></g></svg>
          <span>www.northbeamgrowth.com</span>
        </li>
      </ul>
    </div>
  </section>

</body>
</html>
```